Golf Brochure + Business Card Design Project – Kestrel Fitness.

Task Description

We are looking for a premium tri-fold brochure (8.5x11 letter, folded) plus a new business card design for Kestrel Fitness. Both need to look polished, elegant, and professional — something that would feel at home in a golf club environment.

Brochure Scope:
• Tri-fold brochure promoting our new golf-specific services
• Incorporate brand colors: deep hunter green, cream, and gold accents
• Clean, modern typography (professional, not playful)
• Layout will follow the copy provided (final copy attached, no rewriting needed)
• Imagery: mature golfers (50+), golf lifestyle shots, no generic stocky images
• Include QR code placement linking to booking page
• Deliverables: print-ready PDF with bleed/crop (CMYK), high-res PDF (digital), and source file (InDesign or Illustrator)

Business Card Scope:
• Front + back design
• Consistent with brand colors and fonts
• Space for name, title, phone, email, and website
• Deliverables: print-ready PDF with bleed/crop (CMYK) + source file (AI or InDesign)
• If possible, provide editable template for future staff cards

Timeline:
• First draft within 5–7 days
• 2 rounds of revisions included

Budget:
$300 USD (total for both brochure + business card)

I’ll provide finalized copy if you accept the project.
Project description (paste this whole block in that box)

We need a premium tri-fold brochure (8.5”×11” letter, folded) and a new business card design for Kestrel Fitness. This will be presented to golf course managers and members, so the look must be elegant, restrained, and country-club-classy.

Scope — Brochure
• Format: Tri-fold, 8.5”×11”. Please set 0.125” bleed on all sides and keep critical text ≥0.125–0.25” inside the trim.
• Purpose: Promote Kestrel Fitness’ golf-specific services for adults 50+.
• Copy: We will provide finalized copy in a Word doc after acceptance. No rewriting needed — please focus on layout and polish.
• Imagery (required):
• Golf-first images (ball on tee/green, mature golfers mid-swing, and golf course landscapes at golden hour).
• 1–2 real Kestrel Fitness gym photos on inside panels (trainer with client doing golf-relevant movement: stretch, rotation, balance).
• Visual style: Premium, quiet, lots of white/negative space, balanced grids; no clutter.
• Brand colors (required): Hunter Green #0C2E1F, Gold #CBA135, Cream #F5F2EB. Convert for CMYK print while preserving the look.
• Typography: Clean, legible serif + sans pairing (e.g., modern serif for headlines, humanist/neo-grotesk sans for body). You may propose suitable professional fonts; avoid playful/novelty fonts.
• Elements to include:
• Our logo (we will upload).
• QR code placement to booking page (we will supply the URL / QR asset).
• Simple icon treatment for the three complimentary options (Strength & Mobility, Stretch Therapy, Vitrascan + Assessment).
• Deliverables:
• Print-ready PDF (CMYK, with bleed & crop marks, PDF/X-1a or PDF/X-4)
• High-res digital PDF (no bleed)
• Source file (InDesign or Illustrator) + packaged fonts/links or outlined type as appropriate.

Scope — Business Card
• Size: 3.5”×2” (US standard) with 0.125” bleed; keep text ≥0.125” from trim.
• Front/back design; consistent with brochure branding.
• Fields: Name, Title, Phone, Email, Website, Address; optional small QR on back.
• Deliverables: Print-ready PDF (CMYK, bleed & crops) + Source file (AI/INDD). Provide an editable template for staff names.

Process & Timing
• Initial concept for brochure + card within 5–7 days of acceptance.
• 2 rounds of revisions included.
• Please start with a clean layout concept using placeholder images/text blocks; we’ll drop in final copy/assets immediately after acceptance.

Stock & Licensing
• You may propose stock images that fit the brief (we’re fine approving Pixelgrove or equivalent). Please note any license fees separately if needed.

Usage Rights
• We require full usage rights to the final designs for print & digital.

Target Market(s)

Golfers 50+ in Victoria, BC: quality-oriented, health-conscious, want to play longer, stronger, and pain-free. Country-club aesthetic; expect polished, professional materials.

Industry/Entity Type

Health & Fitness — Golf Performance / Longevity Studio

Font styles to use
Serif
Sans Serif

Requirements
Must have
• • Golf-first imagery + 1–2 real Kestrel Fitness photos inside. • Brand colors: #0C2E1F (Hunter Green), #CBA135 (Gold), #F5F2EB (Cream). • Premium, restrained layout; ample negative space; no clutter. • Clean professional serif + sans type pairing; highly legible. • Space for logo and QR code (booking). • Correct print specs (bleed, crops, CMYK). • Deliverables: print-ready PDFs (brochure + card), digital PDF, source files.
Nice to have
• • Subtle texture or grain in backgrounds (very light) to add sophistication. • A second brochure cover variation (ball on tee vs. course landscape) at concept stage.
Should not have
• • Cheesy/posed “stocky” groups; overly young models; beer/alcohol imagery. • Over-saturated greens/blues; gimmicky gradients or clip art. • Generic fitness/bodybuilding shots unrelated to golf performance.

```html
<!DOCTYPE html>
<html lang="en">
<head>
<meta charset="utf-8">
<title>Kestrel Fitness – Golf Tri-fold Brochure</title>
<link rel="stylesheet" href="https://fonts.googleapis.com/css2?family=Montserrat:wght@300;400;500;700&family=Figtree:wght@400;500&display=swap">
<style>
  :root {
    --page: #e6e6e8;
    --paper: #ffffff;
    --gold: #c6a232;
    --gold-text: #d4ad3a;
    --hunter: #0c3a38;
    --ink: #1d2b2a;
    --ink-soft: #2a3536;
    --night: #0d1314;
    --teal-deep: #103534;
    --white: #ffffff;
    --fold: rgba(0,0,0,0.08);
  }
  * { box-sizing: border-box; margin: 0; padding: 0; }
  html, body { width: 1200px; height: 1200px; overflow: hidden; background: var(--page); }
  .brochure {
    position: absolute; left: 40px; top: 165px;
    width: 1120px; height: 870px;
    background: var(--paper);
    box-shadow: 0 6px 24px rgba(0,0,0,0.12);
    overflow: hidden;
  }
  .panel { position: absolute; top: 0; width: 373.33px; height: 870px; }
  .panel--intro { left: 0; }
  .panel--services { left: 373.33px; }
  .panel--gift { left: 746.66px; }

  /* shared photo across inside panels */
  .gym-photo {
    position: absolute; left: 0; top: 369px; width: 746.66px; height: 501px;
    background: linear-gradient(160deg, #1b2430 0%, #2a3340 35%, #1c1f26 65%, #121418 100%);
  }
  .photo-shapes { position: absolute; left: 0; top: 369px; width: 746.66px; height: 501px; }

  /* intro panel */
  .intro-copy {
    position: absolute; left: 16px; top: 24px; width: 345px;
    font-family: "Figtree", sans-serif; font-size: 12.6px; line-height: 1.55;
    color: var(--ink);
  }
  .intro-copy p { margin-bottom: 16px; }
  .intro-copy ul { list-style: none; margin-bottom: 16px; }
  .intro-copy li { padding-left: 8px; text-indent: -8px; }
  .intro-copy li::before { content: "•"; margin-right: 3px; }

  /* services panel */
  .services-band { position: absolute; left: 0; top: 0; width: 100%; height: 369px; background: var(--gold); }
  .service-list { position: absolute; left: 25px; top: 38px; width: 328px; list-style: none; }
  .service {
    display: flex; align-items: center; height: 71px;
    border-bottom: 1.5px solid rgba(255,255,255,0.8);
    font-family: "Montserrat", sans-serif; font-weight: 400; font-size: 22px;
    color: var(--hunter);
  }
  .service:last-child { border-bottom: none; }
  .service svg { width: 44px; height: 44px; margin-right: 17px; flex: none; }

  .brand-mark {
    position: absolute; left: 160px; top: 270px; width: 200px; height: 200px;
    display: flex; flex-direction: column; align-items: center; justify-content: center;
  }
  .brand-mark .ring { width: 108px; height: 108px; border: 3px solid var(--white); border-radius: 50%; }
  .brand-mark .name {
    margin-top: 12px; font-family: "Montserrat", sans-serif; font-weight: 500;
    font-size: 17px; letter-spacing: 3px; text-transform: uppercase; color: var(--white);
  }

  /* gift panel */
  .gift-bg {
    position: absolute; inset: 0;
    background: linear-gradient(180deg, #0a0f10 0%, #111a1b 30%, #132727 60%, #143434 80%, var(--teal-deep) 100%);
  }
  .gift-content { position: absolute; inset: 0; color: var(--white); font-family: "Montserrat", sans-serif; }
  .gift-title { position: absolute; left: 0; width: 100%; top: 38px; text-align: center; line-height: 1.3; }
  .gift-title .lead { display: block; font-weight: 300; font-size: 32px; }
  .gift-title .accent { display: block; font-weight: 700; font-size: 32px; color: var(--gold-text); }
  .gift-intro { position: absolute; left: 32px; top: 166px; width: 320px; font-size: 13.6px; line-height: 1.52; }
  .choose {
    position: absolute; left: 40px; top: 290px; font-size: 17px; font-weight: 400;
    line-height: 1.5; color: var(--gold-text); text-transform: uppercase;
  }
  .session-list { list-style: none; }
  .session { position: absolute; left: 66px; width: 300px; font-size: 13.6px; line-height: 1.7; }
  .session .num {
    position: absolute; left: -32px; top: -4px; font-size: 32px; font-weight: 300;
    color: transparent; -webkit-text-stroke: 1.2px var(--gold-text); line-height: 1;
  }
  .value { position: absolute; left: 32px; top: 740px; font-size: 14.5px; }
  .value small { display: block; font-size: 11px; margin-top: 4px; }
  .redeem { position: absolute; left: 32px; top: 798px; font-size: 14.5px; }
  .redeem small { display: block; font-size: 11px; margin-top: 4px; }

  .fold { position: absolute; top: 0; width: 1px; height: 870px; background: var(--fold); }
</style>
</head>
<body>
<article class="brochure">

  <div class="gym-photo" role="img" aria-label="Gym photo: trainer coaching a mature golfer through rotational cable and stance drills"></div>
  <svg class="photo-shapes" viewBox="0 0 746.66 501" preserveAspectRatio="none" aria-hidden="true">
    <polygon points="0,0 373.33,0 0,86" fill="var(--gold)"/>
    <polygon points="746.66,419 746.66,501 437,501" fill="var(--hunter)"/>
  </svg>

  <section class="panel panel--intro">
    <div class="intro-copy">
      <p>The game changes as we age. Distance fades, flexibility tightens, and recovery after 18 holes takes longer than it used to. But that doesn’t mean your best golf is behind you.</p>
      <p>At Kestrel Fitness, we specialize in helping golfers 50+ build the strength, mobility, and balance needed to:</p>
      <ul>
        <li>Add yards off the tee with rotational strength training</li>
        <li>Maintain a fluid swing with improved shoulder and hip mobility</li>
        <li>Reduce back and joint pain with targeted stability work</li>
        <li>Walk off the 18th green feeling strong, not sore</li>
      </ul>
      <p>This isn’t generic gym training — it’s science-based coaching tailored to golfers.</p>
    </div>
  </section>

  <section class="panel panel--services">
    <div class="services-band"></div>
    <ul class="service-list">
      <li class="service">
        <svg viewBox="0 0 44 44" fill="none" stroke="var(--hunter)" stroke-width="1.8" stroke-linecap="round">
          <path d="M8 14a17 17 0 0 1 28-2M36 30a17 17 0 0 1-28 2"/>
          <path d="M36 6v6h-6M8 38v-6h6"/>
          <rect x="12" y="17" width="5" height="10" rx="1"/><rect x="27" y="17" width="5" height="10" rx="1"/>
          <path d="M17 22h10"/>
        </svg>
        Strength &amp; Mobility
      </li>
      <li class="service">
        <svg viewBox="0 0 44 44" fill="none" stroke="var(--hunter)" stroke-width="1.8" stroke-linecap="round">
          <rect x="4" y="30" width="36" height="5" rx="2"/>
          <path d="M4 39h36"/>
          <circle cx="24" cy="10" r="4"/>
          <path d="M24 15v10M18 25h12"/>
        </svg>
        Stretch Therapy
      </li>
      <li class="service">
        <svg viewBox="0 0 44 44" fill="none" stroke="var(--hunter)" stroke-width="1.8" stroke-linecap="round">
          <rect x="6" y="6" width="24" height="32" rx="2"/>
          <path d="M14 4h8v5h-8z"/>
          <path d="M10 16h3M16 16h9M10 22h3M16 22h9M10 28h3M16 28h6"/>
          <circle cx="32" cy="30" r="8"/>
          <path d="M32 26v4h3"/>
        </svg>
        Vitrascan + Assessment
      </li>
    </ul>
    <div class="brand-mark">
      <div class="ring"></div>
      <div class="name">Kestrel Fitness</div>
    </div>
  </section>

  <section class="panel panel--gift">
    <div class="gift-bg" role="img" aria-label="Darkened gym interior behind the offer text"></div>
    <div class="gift-content">
      <h2 class="gift-title"><span class="lead">Your Exclusive</span><span class="accent">Member Gift</span></h2>
      <p class="gift-intro">As one of the club’s most valued golfers, you’ve been hand-selected to receive a complimentary premium experience at Kestrel Fitness.</p>
      <p class="choose">Choose one<br>golf-specific session:</p>
      <ol class="session-list">
        <li class="session" style="top:370px"><span class="num">1</span>Golf Strength &amp; Mobility Session Add rotational power for more distance and protect your back.</li>
        <li class="session" style="top:455px"><span class="num">2</span>Golf Flexibility &amp; Stretch Therapy Unlock tighter hips &amp; shoulders to swing easier and play longer.</li>
        <li class="session" style="top:541px"><span class="num">3</span>Vitrascan + Golf Wellness Assessment Identify muscle imbalances and posture issues holding your game back.</li>
        <li class="session" style="top:626px"><span class="num">4</span>Golf Strength &amp; Mobility Session Add rotational power for more distance and protect your back.</li>
      </ol>
      <p class="value">Valued at $110–$125<small>(Reserved exclusively for select golf members)</small></p>
      <p class="redeem">To redeem: Contact Kestrel Fitness directly.<small>This invitation is limited and not available to the public.</small></p>
    </div>
  </section>

  <div class="fold" style="left:373px"></div>
  <div class="fold" style="left:746px"></div>
</article>
</body>
</html>
```